Business Card Makeover. Recreate a sleek modern design for our business card.

DO NOT COPY OUR CURRENT DESIGN. MUST BE ONE SIDED BUSINESS CARD.
Create a new business card design, using our new logo. Attached is a sample of our current design and new logo. Please note the address and email will change. The new address is 412 Corvell West Palm Beach 33401 and our website will be www.delmarhollis.example.

We are an architectural and interior design firm. We prefer a clean modern look. Something that is refined and emulates excellence.

Industry/Entity Type

Architecture

Contact Information for Business Card

clean modern look, please do not copy our attached design.

Font styles to use
Other font styles liked:
• see attached business card font

Colors

Designer to choose colors to be used in the design.

Requirements
Must have
• Must have a modern appeal and resemble our current branding.
Nice to have
• modern font, our logo, legible name and titles progressive design
Should not have
• Do not add colors not reflected in our branding. Should not look like our current card.

```html
<!DOCTYPE html>
<html lang="en">
<head>
<meta charset="utf-8">
<title>Delmar Hollis – Business Cards</title>
<link rel="stylesheet" href="https://fonts.googleapis.com/css2?family=Open+Sans:wght@400;600&family=Playfair+Display:wght@500&display=swap">
<style>
  :root {
    --backdrop: #dcdcdc;
    --card: #333233;
    --ink: #ffffff;
    --ink-soft: #e6e6e6;
    --rule: #bdbdbd;
    --accent: #1f5fbf;
    --icon-neutral: #d0d0d0;
  }
  * { margin: 0; padding: 0; box-sizing: border-box; }
  html, body { width: 1200px; height: 800px; overflow: hidden; }
  body {
    background: var(--backdrop);
    font-family: "Open Sans", sans-serif;
    color: var(--ink);
    position: relative;
  }
  .card {
    position: absolute;
    top: 272px;
    width: 473px;
    height: 263px;
    background: var(--card);
  }
  .card--graham { left: 60px; }
  .card--nadia { left: 642px; }

  .brand {
    position: absolute;
    left: 88px;
    top: 20px;
    display: flex;
    align-items: center;
    gap: 12px;
  }
  .brand__dot {
    width: 58px; height: 58px;
    border-radius: 50%;
    background: var(--ink);
  }
  .brand__name {
    font-size: 25px;
    font-weight: 400;
    letter-spacing: 1px;
    color: var(--ink);
  }
  .tagline {
    position: absolute;
    left: 165px;
    top: 82px;
    font-size: 12px;
    letter-spacing: 1.1px;
    color: var(--ink);
  }

  .person {
    position: absolute;
    left: 27px;
  }
  .card--graham .person { top: 154px; }
  .card--nadia .person { top: 144px; }
  .person__name {
    font-family: "Playfair Display", serif;
    font-weight: 500;
    font-size: 20px;
    letter-spacing: 0.6px;
    line-height: 26px;
  }
  .person__line {
    font-size: 11px;
    line-height: 16px;
    color: var(--ink-soft);
  }

  .rule {
    position: absolute;
    left: 24px;
    top: 201px;
    width: 426px;
    height: 1px;
    background: var(--rule);
  }

  .contact {
    position: absolute;
    left: 0;
    width: 100%;
    top: 207px;
    text-align: center;
    font-size: 11.5px;
    line-height: 16.5px;
  }
  .card--graham .contact { padding-left: 30px; }
  .contact__row { display: flex; justify-content: center; gap: 12px; }
  .contact__item { display: inline-flex; align-items: center; gap: 4px; }
  .icon {
    width: 8px; height: 8px;
    border-radius: 50%;
    background: var(--icon-neutral);
  }
  .card--nadia .icon { background: var(--accent); }
</style>
</head>
<body>

  <section class="card card--graham">
    <div class="brand">
      <span class="brand__dot"></span>
      <span class="brand__name">DELMAR HOLLIS</span>
    </div>
    <p class="tagline">Architecture + Interior Design</p>
    <div class="person">
      <h2 class="person__name">Graham Whitlock</h2>
      <p class="person__line">Partner / Project of Desgin</p>
    </div>
    <div class="rule"></div>
    <div class="contact">
      <div class="contact__row">
        <span class="contact__item"><span class="icon"></span>561.555.0142</span>
        <span class="contact__item"><span class="icon"></span>561.555.0187</span>
        <span class="contact__item"><span class="icon"></span>561.555.0163</span>
      </div>
      <div class="contact__row">
        <span class="contact__item"><span class="icon"></span>118 Larkin Street, West Palm Beach, FL 33401</span>
      </div>
      <div class="contact__row">
        <span class="contact__item"><span class="icon"></span>graham@delmarhollis.example</span>
        <span class="contact__item"><span class="icon"></span>www.delmarhollis.example</span>
      </div>
    </div>
  </section>

  <section class="card card--nadia">
    <div class="brand">
      <span class="brand__dot"></span>
      <span class="brand__name">DELMAR HOLLIS</span>
    </div>
    <p class="tagline">Architecture + Interior Design</p>
    <div class="person">
      <h2 class="person__name">Nadia Ferrell</h2>
      <p class="person__line">AIA, LEED ® AP</p>
      <p class="person__line">Partner / Project Architect</p>
    </div>
    <div class="rule"></div>
    <div class="contact">
      <div class="contact__row">
        <span class="contact__item"><span class="icon"></span>561.555.0142</span>
        <span class="contact__item"><span class="icon"></span>561.555.0163</span>
      </div>
      <div class="contact__row">
        <span class="contact__item"><span class="icon"></span>412 Corvell, West Palm Beach 33401</span>
      </div>
      <div class="contact__row">
        <span class="contact__item"><span class="icon"></span>nadia@delmarhollis.example</span>
        <span class="contact__item"><span class="icon"></span>www.delmarhollis.example</span>
      </div>
    </div>
  </section>

</body>
</html>
```